Leadership training for women Business + Spirit

I need a flyer for a leadership training to hand out after I've been doing public speaking. I would also like to send it as a PDF. so maybe A4 is a good size. I will probably also need a brochure, with some more in depth information, but to start with I like to just give them something so they get inspired to contact me for more information. You can see more of my style on www.brightmeadow.se . Its a training that combines business with spirit, heart with intellect. We focus both on strict leadership skills such as Setting objectives aligned with strategy, assess performance and spiritual practices such as meditation, connecting with your unique essence. I like the deign to communicate business and professional together with warmth, life and joy. Colourful with style. Empowerment. The attached style guide does not have to be followed strictly but please use it in combination with my site www.brightmeadow.se I've the logo in many different sizes. I've added the smallest one below. Use any images that you think might fit, doesn't have to be from my website, it could be from your resources. I've added some other images here in the brief too, I have many more but can't attach all of it :-).
Target Market(s)
Women in leadership positions age 30 - 60
Industry/Entity Type
Leadership
Look and feel

```html
<!DOCTYPE html>
<html lang="sv">
<head>
<meta charset="utf-8">
<title>BrightMeadow – Att Leda Är Att Lyckas Genom Andra</title>
<link rel="stylesheet" href="https://fonts.googleapis.com/css2?family=Montserrat:wght@400;500;600;700&family=Roboto+Condensed:wght@700&display=swap">
<style>
  :root {
    --stage: #e6e7e9;
    --paper: #ffffff;
    --ink-dark: #0e141c;
    --navy: #1d3452;
    --navy-deep: #15263d;
    --text: #34404f;
    --muted: #8d96a2;
    --quote-grey: #c3c8ce;
    --white: #ffffff;
  }
  * { box-sizing: border-box; margin: 0; padding: 0; }
  html, body { width: 1200px; height: 986px; overflow: hidden; background: var(--stage); }
  body { font-family: "Montserrat", sans-serif; color: var(--text); }

  .flyer {
    position: absolute; left: 270px; top: 24px;
    width: 660px; height: 938px;
    background: var(--paper);
    box-shadow: 0 8px 28px rgba(0,0,0,.18);
    overflow: hidden;
  }

  /* Header */
  .hero { position: relative; height: 320px; background: var(--ink-dark); }
  .hero-photo {
    position: absolute; right: 0; top: 0; width: 440px; height: 290px;
    background: radial-gradient(ellipse at 55% 40%, #5b5f66 0%, #2c3038 45%, #12161d 80%);
  }
  .hero-fade {
    position: absolute; left: 0; top: 0; width: 320px; height: 290px;
    background: linear-gradient(90deg, var(--ink-dark) 55%, rgba(14,20,28,0));
  }
  .brand { position: absolute; left: 28px; top: 26px; display: flex; align-items: center; gap: 10px; }
  .brand-dot { width: 36px; height: 36px; border-radius: 50%; border: 1.5px solid var(--white); }
  .brand-name { font-size: 22px; font-weight: 500; color: var(--white); line-height: 1; }
  .brand-tag { font-size: 7px; letter-spacing: .12em; color: var(--white); margin-top: 4px; }
  .hero-title {
    position: absolute; left: 34px; top: 150px;
    font-family: "Roboto Condensed", sans-serif; font-weight: 700; color: var(--white);
    line-height: 1;
  }
  .hero-title .line1 { display: block; font-size: 40px; }
  .hero-title .line2 { display: block; font-size: 25px; margin-top: 4px; padding-left: 14px; }
  .hero-band { position: absolute; left: 0; bottom: 0; width: 660px; height: 80px; }

  /* Body */
  .content { padding: 18px 30px 0; font-size: 11px; line-height: 1.45; }
  .intro { margin-bottom: 20px; }
  .columns { display: grid; grid-template-columns: 1fr 1fr; gap: 26px; }
  .section-title {
    font-size: 14px; font-weight: 700; color: var(--navy);
    text-transform: uppercase; line-height: 1.2; margin-bottom: 10px;
  }
  .lead-in { font-weight: 700; color: var(--navy); margin-bottom: 8px; }
  .ticks { list-style: none; margin-bottom: 20px; }
  .ticks li { position: relative; padding-left: 16px; margin-bottom: 2px; }
  .ticks li::before {
    content: ""; position: absolute; left: 0; top: 4px;
    width: 8px; height: 8px; border-radius: 50%; background: var(--navy);
  }

  .quote {
    position: relative; margin-top: 18px; padding: 26px 24px 26px;
    border: 1px solid var(--muted); border-radius: 6px;
    font-size: 10px;
  }
  .quote-mark {
    position: absolute; font-family: "Roboto Condensed", sans-serif;
    font-size: 64px; color: var(--quote-grey); line-height: 1; background: var(--paper); padding: 0 4px;
  }
  .quote-mark.open { left: -8px; bottom: -34px; }
  .quote-mark.close { right: -8px; top: -16px; }
  .quote strong { color: var(--navy); }

  /* Footer */
  .footer {
    position: absolute; left: 0; bottom: 0; width: 660px; height: 50px;
    background: var(--navy);
    display: flex; align-items: center; justify-content: space-between;
    padding: 0 20px; color: var(--white); font-size: 13px;
  }
  .footer-item { display: flex; align-items: center; gap: 7px; white-space: nowrap; }
  .footer-item svg { width: 15px; height: 15px; }
  .social-square { width: 20px; height: 20px; border-radius: 3px; background: var(--white); }
  .footer-edge { position: absolute; left: 0; bottom: 50px; width: 660px; height: 6px; background: var(--navy-deep); }
</style>
</head>
<body>
  <article class="flyer">
    <header class="hero">
      <div class="hero-photo" role="img" aria-label="Foto av en kvinnlig ledare vid en bärbar dator i ett mörkt kontor"></div>
      <div class="hero-fade"></div>
      <div class="brand">
        <span class="brand-dot"></span>
        <div>
          <div class="brand-name">BrightMeadow</div>
          <div class="brand-tag">LEDARSKAP MED HJÄRTA OCH SJÄL</div>
        </div>
      </div>
      <h1 class="hero-title">
        <span class="line1">Att Leda Är Att</span>
        <span class="line2">Lyckas Genom Andra</span>
      </h1>
      <svg class="hero-band" viewBox="0 0 660 80" preserveAspectRatio="none" aria-hidden="true">
        <path d="M0 30 C 200 60, 430 60, 660 0 L660 80 L0 80 Z" fill="#1d3452"/>
        <path d="M0 52 C 200 78, 430 78, 660 26 L660 80 L0 80 Z" fill="#ffffff"/>
      </svg>
    </header>

    <main class="content">
      <p class="intro">Visste du att det finns sätt att driva resultat där vi på riktigt förenar det inre med det yttre och tillåter oss att bli genuint starkare för varje dag? Den här ledarskapsutbildning fokuserar på det. Den är till för dig som gillar att prestera och redan är intresserad av personlig utveckling, andligt uppvaknande och vill leva ett meningsfullt liv. I yrkeslivet är du en ledare som trivs med framgång och högt tempo men vill hitta platsen där du utvecklas som själ likväl som chef. Den här utbildningen kommer att förankra dig både i en kraft och specifika färdigheter som ger dig möjlighet att fortsätta göra det du är bra på, utan att kompromissa kontakten med det som egentligen betyder mest för dig.</p>

      <div class="columns">
        <section>
          <h2 class="section-title">Andlighet, prestation<br>och ledarskap</h2>
          <ul class="ticks">
            <li>Hur du kan vara i arbetslivet utan att kompromissa kontakten med hjärtat och din inre visdom.</li>
            <li>Sätt tydliga mål och kommunicera effektivt.</li>
            <li>Förbereda och genomföra svåra samtal.</li>
            <li>Delegering som frigör tid för ditt ledarskap, utvecklar dina medarbetare och stärker ditt team.</li>
            <li>Coacha medarbetare och ledare.</li>
            <li>Rota dig i din egna unika essens för att leva ett själfullt liv.</li>
            <li>Att låta din kropp och sinne arbeta för dig, inte emot.</li>
          </ul>
          <p>Du kommer dessutom hitta ett nätverk av andra visa kvinnor att dela utmaningarna i ledarrollen med. Kvinnor som även de värderar kontakten med hjärtat och själen likväl som yttre framgång och ett gott materiellt liv. Tillsammans får ni möjlighet att kombinera den inre längtan efter ett andligt djup med höga krav på lönsamhet eller resultat.</p>
        </section>

        <section>
          <p class="lead-in">Du kommer att lämna utbildningen påfylld, inspirerad och väl förberedd med:</p>
          <ul class="ticks">
            <li>Personlig utvecklingsplan för ditt ledarskap</li>
            <li>En konkret handlingsplan</li>
            <li>Kontakt med något större, den du är bortom alla roller</li>
            <li>Ny förståelse för hur du kan få det inre och yttre att skapa synergi istället för kompromiss</li>
            <li>Ett nätverk av andra visa kvinnor som också längtar efter att kunna dela både utmaningar i ledarrollen och den inre längtan efter mer själ och hjärta i livet..</li>
          </ul>
          <blockquote class="quote">
            <span class="quote-mark close">”</span>
            Verkligen en härlig överraskning att hamna på en föreläsning som satte fingret på den kombo av ledarskap och personlig utveckling som jag alltid sökt! – <strong>Helena</strong>
            <span class="quote-mark open">“</span>
          </blockquote>
        </section>
      </div>
    </main>

    <div class="footer-edge"></div>
    <footer class="footer">
      <span class="footer-item">
        <svg viewBox="0 0 16 16" aria-hidden="true"><path d="M4 1.5 L6 5 L4.6 6.4 C5.5 8.3 7.7 10.5 9.6 11.4 L11 10 L14.5 12 L13 14.5 C8 14.5 1.5 8 1.5 3 Z" fill="#fff"/></svg>
        0739-55 18 40
      </span>
      <span class="footer-item">
        <svg viewBox="0 0 16 16" aria-hidden="true"><rect x="1.5" y="3.5" width="13" height="9" rx="1" fill="none" stroke="#fff" stroke-width="1.4"/><path d="M1.5 4 L8 9 L14.5 4" fill="none" stroke="#fff" stroke-width="1.4"/></svg>
        maria(a)brightmeadow.se
      </span>
      <span class="footer-item">
        <svg viewBox="0 0 16 16" aria-hidden="true"><circle cx="8" cy="8" r="6.3" fill="none" stroke="#fff" stroke-width="1.4"/><path d="M1.7 8 H14.3 M8 1.7 C5 5 5 11 8 14.3 M8 1.7 C11 5 11 11 8 14.3" fill="none" stroke="#fff" stroke-width="1.2"/></svg>
        www.brightmeadow.se
      </span>
      <span class="footer-item">Follow us <span class="social-square"></span></span>
    </footer>
  </article>
</body>
</html>
```